Corvel Capital LLC

Need Professional Business cards for New Investment Fund

Target Market(s)

High Quality investors

Industry/Entity Type

Financial

Contact Information for Business Card

Phone Number +1 555 284 6190
Name Lukas Varenko
Title Fund Manager
email lv@FundCorvel.com
Website www.FundCorvel.com

Colors

Designer to choose colors to be used in the design.

Requirements
Must have
• Must have our Logo and all of the above. Must be made so lettering and loge can be raised

```html
<!DOCTYPE html>
<html lang="en">
<head>
<meta charset="utf-8">
<title>Orsivane – Business Card</title>
<link rel="stylesheet" href="https://fonts.googleapis.com/css2?family=Roboto:wght@400;500;700&display=swap">
<style>
  :root {
    --backdrop: #d8d1c7;
    --card-light: #e9e7e3;
    --panel-dark: #3b3f3c;
    --accent-green: #8cc63f;
    --text-light: #e6e6e3;
    --logo-dark: #3a3e3b;
  }
  html, body {
    margin: 0;
    width: 1200px;
    height: 1054px;
    overflow: hidden;
    background: var(--backdrop);
    font-family: 'Roboto', Arial, sans-serif;
  }
  .card {
    position: absolute;
    left: 150px;
    top: 270px;
    width: 900px;
    height: 514px;
    background: var(--card-light);
    overflow: hidden;
    box-shadow: 0 10px 30px rgba(0,0,0,0.18);
  }
  .card-shapes {
    position: absolute;
    inset: 0;
  }
  .identity {
    position: absolute;
    left: 40px;
    top: 72px;
  }
  .person-name {
    margin: 0;
    font-size: 31px;
    font-weight: 700;
    color: var(--accent-green);
    letter-spacing: 0.2px;
  }
  .person-title {
    margin: 8px 0 0;
    font-size: 21px;
    font-weight: 400;
    color: var(--text-light);
  }
  .contacts {
    position: absolute;
    left: 40px;
    top: 372px;
    margin: 0;
    padding: 0;
    list-style: none;
  }
  .contact-item {
    display: flex;
    align-items: center;
    height: 34px;
    font-size: 21px;
    color: var(--text-light);
  }
  .contact-icon {
    width: 20px;
    height: 20px;
    margin-right: 26px;
    fill: var(--accent-green);
  }
  .brand-name {
    position: absolute;
    left: 600px;
    top: 248px;
    width: 280px;
    margin: 0;
    text-align: center;
    font-size: 48px;
    font-weight: 500;
    letter-spacing: 2px;
    color: var(--logo-dark);
  }
</style>
</head>
<body>
  <div class="card">
    <svg class="card-shapes" width="900" height="514" viewBox="0 0 900 514">
      <path class="dark-panel" d="M0 0 H516 C452 120 432 300 505 514 H0 Z" fill="var(--panel-dark)"/>
      <path class="accent-curve" d="M516 0 C452 120 432 300 505 514 L490 514 C438 330 440 150 516 0 Z" fill="var(--accent-green)"/>
    </svg>

    <div class="identity">
      <h1 class="person-name">Lukas Varenko</h1>
      <p class="person-title">Fund Manager</p>
    </div>

    <ul class="contacts">
      <li class="contact-item">
        <svg class="contact-icon" viewBox="0 0 20 20"><path d="M2 7 C2 4 6 3 10 3 C14 3 18 4 18 7 L15 8 L14 6 H6 L5 8 Z M5 10 H15 L17 17 H3 Z"/></svg>
        +1 555 284 6190
      </li>
      <li class="contact-item">
        <svg class="contact-icon" viewBox="0 0 20 20"><path d="M2 4 H18 V16 H2 Z M3.5 5.5 L10 11 L16.5 5.5 Z" fill-rule="evenodd"/></svg>
        lv@FundCorvel.com
      </li>
      <li class="contact-item">
        <svg class="contact-icon" viewBox="0 0 20 20"><circle cx="10" cy="10" r="8"/><path d="M2 10 H18 M10 2 V18 M4 6 H16 M4 14 H16" stroke="var(--panel-dark)" stroke-width="1" fill="none"/></svg>
        www.FundCorvel.com
      </li>
    </ul>

    <p class="brand-name">ORSIVANE</p>
  </div>
</body>
</html>
```